Business card design Needed for new logo / Construction business, home extensions and new builds

We need a business card design using our new logo files which i will attach to this project :)

We are a small construction business specialising in home extensions, new builds and property development. We are very ambitious and would appreciate professional and elegant designs for our new business card.

Very serious about using the services on MakerQuarry and recently acquired our new logo from here :)

Please get involved, i will feedback when i can as i am very busy but can respond daily, thanks

Target Market(s)

People that want to build onto their houses, new building developments or adding too their existing property

Industry/Entity Type

Construction

Contact Information for Business Card

Renwick Tolliver Construction, Lionel Ashby (Managing Director), Tel 07822254961, email - info@renwick-tolliver, www.renwick-tolliver.co.uk

Colors

Designer to choose colors to be used in the design.

Requirements
Must have
• I like a deep grey on the back please. A lot of you have provided black from and back, try mixing things up a little. The black looks cool 😎 Thanks

```html
<!DOCTYPE html>
<html lang="en">
<head>
<meta charset="utf-8">
<title>Renwick Tolliver Construction – Business Card</title>
<link rel="stylesheet" href="https://fonts.googleapis.com/css2?family=Cinzel:wght@400;600&family=EB+Garamond:wght@400;500&display=swap">
<style>
  :root {
    --backdrop: #3b3b3d;
    --card-back: #1f1f21;
    --card-front: #161617;
    --silver: #d9dadc;
    --gold: #d9a534;
    --gold-light: #f3cf68;
    --divider: #3a3a3c;
  }
  * { box-sizing: border-box; margin: 0; padding: 0; }
  html, body { width: 1200px; height: 689px; overflow: hidden; }
  body {
    background: var(--backdrop);
    display: flex;
    align-items: center;
    justify-content: center;
    gap: 40px;
    font-family: "EB Garamond", Georgia, serif;
  }
  .card {
    position: relative;
    width: 540px;
    height: 309px;
    border-radius: 18px;
    overflow: hidden;
    box-shadow: 0 14px 30px rgba(0,0,0,.45);
  }

  /* Back side */
  .card--back { background: var(--card-back); }
  .card--back .wordmark {
    position: absolute;
    right: 44px;
    bottom: 70px;
    text-align: right;
  }

  .wordmark-name {
    font-family: "Cinzel", "Times New Roman", serif;
    font-weight: 400;
    color: var(--silver);
    letter-spacing: .04em;
    line-height: 1.15;
  }
  .card--back .wordmark-name { font-size: 27px; }

  .wordmark-rule {
    display: flex;
    align-items: center;
    gap: 10px;
    margin-top: 4px;
  }
  .wordmark-rule::before,
  .wordmark-rule::after {
    content: "";
    flex: 1;
    height: 1.5px;
    background: var(--gold);
  }

  /* Front side */
  .card--front { background: var(--card-front); }
  .card--front .wordmark {
    position: absolute;
    left: 38px;
    top: 118px;
    width: 230px;
    text-align: center;
  }
  .card--front .wordmark-name { font-size: 22px; }

  .divider {
    position: absolute;
    left: 292px;
    top: 48px;
    width: 1px;
    height: 190px;
    background: var(--divider);
  }

  .contact {
    position: absolute;
    left: 312px;
    top: 46px;
    color: var(--silver);
  }
  .contact-name {
    font-family: "Cinzel", "Times New Roman", serif;
    font-size: 19px;
    letter-spacing: .03em;
    line-height: 1.1;
  }
  .contact-role {
    color: var(--gold);
    font-size: 14px;
    margin-bottom: 16px;
  }
  .contact-list { list-style: none; }
  .contact-list li {
    display: flex;
    align-items: center;
    gap: 7px;
    font-size: 13.5px;
    line-height: 1.55;
  }
  .contact-list svg { width: 11px; height: 11px; flex: none; }
  .contact-address {
    margin-top: 18px;
    font-size: 13.5px;
    line-height: 1.35;
    font-style: normal;
  }

  .gold-band {
    position: absolute;
    left: 0;
    right: 0;
    bottom: 0;
    height: 9px;
    background: linear-gradient(90deg, var(--gold), var(--gold-light) 45%, var(--gold) 75%, var(--gold-light));
  }
</style>
</head>
<body>

  <section class="card card--back" aria-label="Card back">
    <div class="wordmark">
      <div class="wordmark-name">Renwick Tolliver</div>
      <div class="wordmark-name">Construction</div>
      <div class="wordmark-rule"></div>
    </div>
  </section>

  <section class="card card--front" aria-label="Card front">
    <div class="wordmark">
      <div class="wordmark-name">Renwick Tolliver</div>
      <div class="wordmark-name">Construction</div>
      <div class="wordmark-rule"></div>
    </div>

    <div class="divider"></div>

    <div class="contact">
      <div class="contact-name">LIONEL ASHBY</div>
      <div class="contact-role">Managing Director</div>
      <ul class="contact-list">
        <li>
          <svg viewBox="0 0 12 12" aria-hidden="true"><path d="M3 1 L5 3.5 L4 4.8 Q5 7 7.2 8 L8.5 7 L11 9 L10 11 Q4.5 11 1 2 Z" fill="var(--silver)"/></svg>
          07700 900461
        </li>
        <li>
          <svg viewBox="0 0 12 12" aria-hidden="true"><rect x="1" y="2.5" width="10" height="7" fill="var(--silver)"/><path d="M1 2.5 L6 6.5 L11 2.5" fill="none" stroke="var(--card-front)" stroke-width="1"/></svg>
          info@renwick-tolliver
        </li>
        <li>
          <svg viewBox="0 0 12 12" aria-hidden="true"><circle cx="6" cy="6" r="5" fill="none" stroke="var(--silver)" stroke-width="1"/><ellipse cx="6" cy="6" rx="2.2" ry="5" fill="none" stroke="var(--silver)" stroke-width=".8"/><path d="M1 6 H11 M2 3.5 H10 M2 8.5 H10" stroke="var(--silver)" stroke-width=".8"/></svg>
          www.renwick-tolliver.co.uk
        </li>
      </ul>
      <address class="contact-address">
        17 Marlow Quarry Road<br>
        Hallbridge, HB4 2QT
      </address>
    </div>

    <div class="gold-band"></div>
  </section>

</body>
</html>
```